Property Finance Company - Orbin Funding Limited

Background: Orbin Funding Group Limited is a private property finance company. Orbin Funding Group has capital to directly fund first mortgage, mezzanine and preferred equity financing. We also acquire performing, sub-performing and distressed debt.

Orbin Fundings management philosophy emphasises expertise, innovation, wisdom, honesty and competitiveness. Orbin Funding are not finance brokers - we provide debt funding to the commercial property and residential development sectors. Our process is built from experience and cumutavely Orbin Fundings Directors have in excess of 60 years wisdom.

The aim of the website will be to increase brand awareness, provide clients with comfort around our level of skill and background on who we are, generate more sales, and provide examples of projects that we have funded.

The website is a new product launch, and we need to use our Orbin Funding logo that has just been designed. We like a dark background, and either black/silver/grey/ jade green, or black/gold/jade green colours.

Our unique advantages are that we have fast turnaround times, we can solve clients funding problems and we know what we are doing. Our target audience will be viewing the website on both desktop and mobile devices.

We would like to have the following pages:

Home
About
Team
Services
Project Experience
Contact

Competitors Website: http://www.tarvolo.example/

We would also like to have the option of video footage in our website, as you can see in our competitors website.

Overall we want a really slick, elegant but modern website that is better than www.tarvolo.example

Target Market(s)

Finance borrowers, property developers, accountants, lawyers, businesspeople, high net worth people

Industry/Entity Type

Finance

Requirements
Must have
• Please see project description
Nice to have
Should not have

```html
<!DOCTYPE html>
<html lang="en">
<head>
<meta charset="utf-8">
<title>Orbin Funding Group</title>
<link rel="stylesheet" href="https://fonts.googleapis.com/css2?family=Lora:wght@400;700&family=Open+Sans:wght@400;600&display=swap">
<style>
:root{
  --jade:#1e9a5a;
  --ink:#2f2f2f;
  --panel:#333333;
  --footer:#2b2b2b;
  --text:#333;
  --muted:#b9b9b9;
  --white:#fff;
}
*{box-sizing:border-box;margin:0;padding:0}
html,body{width:1200px;height:2691px;overflow:hidden;background:var(--white)}
body{font-family:"Open Sans",Arial,sans-serif;color:var(--text);position:relative}

/* Header */
.top-bar{position:absolute;left:0;top:0;width:1200px;height:145px;overflow:hidden;
  background:linear-gradient(90deg,#8d8d8d 0%,#e2e2e2 25%,#bdbdbd 50%,#cfcfcf 70%,#9a9a9a 100%)}
.top-bar .stripes{position:absolute;left:0;top:0}
.brand{position:absolute;left:128px;top:18px;width:160px;display:flex;flex-direction:column;align-items:center;gap:8px}
.brand-mark{width:50px;height:50px;border-radius:50%;background:#555}
.brand-name{font-family:"Lora",Georgia,serif;font-size:17px;color:#3a3a3a;letter-spacing:.5px;text-align:center;line-height:20px;white-space:nowrap}
.brand-name .sub{display:block;font-size:13px;letter-spacing:3px;line-height:16px}
.contact-info{position:absolute;right:133px;top:40px;text-align:right;color:var(--white)}
.contact-info .phone{font-family:"Lora",Georgia,serif;font-size:23px;line-height:28px;display:flex;align-items:center;justify-content:flex-end;gap:12px;white-space:nowrap}
.contact-info .phone svg,.contact-info .email svg{flex:none}
.contact-info .email{font-size:14px;line-height:18px;margin-top:10px;display:flex;align-items:center;justify-content:flex-end;gap:9px;white-space:nowrap}

.main-nav{position:absolute;left:0;top:145px;width:1200px;height:42px;background:linear-gradient(90deg,#2a2a2a,#3a3a3a 60%,#454545)}
.main-nav ul{list-style:none;display:flex;position:absolute;left:133px;top:13px;gap:30px}
.main-nav a{font-family:"Lora",Georgia,serif;font-size:13px;color:var(--white);text-decoration:none;text-transform:uppercase;letter-spacing:.3px}
.main-nav a.current{text-decoration:underline}
.social{position:absolute;right:133px;top:13px;display:flex;gap:22px}
.social span{width:14px;height:14px;border-radius:50%;background:#bdbdbd;display:block}

/* Hero */
.hero{position:absolute;left:0;top:187px;width:1200px;height:428px;
  background:linear-gradient(180deg,#9aa8b8 0%,#c9b7a6 45%,#6d6a66 75%,#3d3f44 100%)}
.hero .play{position:absolute;left:574px;top:188px;width:52px;height:52px}

/* Welcome */
.welcome{position:absolute;left:133px;top:700px;width:934px;text-align:center}
.welcome h1{font-family:"Lora",Georgia,serif;font-weight:400;color:var(--jade);font-size:32px;text-transform:uppercase;letter-spacing:.3px}
.welcome p{font-size:13.5px;line-height:23px;margin-top:22px;color:#333}
.welcome p+p{margin-top:20px}
.btn{display:inline-block;background:var(--jade);color:var(--white);font-family:"Lora",Georgia,serif;font-size:14px;text-decoration:none;padding:0 18px;height:40px;line-height:40px}
.welcome .btn{margin-top:26px;width:128px;padding:0}

/* Services */
.services{position:absolute;left:133px;top:1035px;width:934px;display:grid;grid-template-columns:467px 467px;grid-auto-rows:304px}
.service-text{background:var(--panel);padding:30px 28px;color:var(--white)}
.service-text h2{font-family:"Lora",Georgia,serif;font-weight:400;font-size:24px;line-height:30px;text-transform:uppercase}
.service-text p{font-size:11px;line-height:20px;color:var(--muted);margin-top:12px}
.outline-btn{display:inline-block;margin-top:18px;border:1px solid #999;color:#ccc;font-family:"Lora",Georgia,serif;font-size:13px;padding:10px 18px;text-decoration:none}
.photo{display:block}
.photo-desk{background:linear-gradient(135deg,#f4f6f8,#cfd8de 60%,#9fb3c0)}
.photo-coins{background:radial-gradient(circle at 30% 30%,#e9c27a,#a5692a 55%,#4b2e16)}
.photo-blue{background:linear-gradient(135deg,#b9d6ee,#3a78b8 55%,#0f2d5a)}

/* Projects */
.projects{position:absolute;left:133px;top:2030px;width:934px;text-align:center}
.projects h2{font-family:"Lora",Georgia,serif;font-weight:400;color:var(--jade);font-size:24px;text-transform:uppercase}
.project-row{display:flex;gap:7px;margin-top:18px}
.project-row div{width:228px;height:228px}
.p1{background:linear-gradient(180deg,#5b6f86,#2c3a4a 60%,#6e6a63)}
.p2{background:linear-gradient(180deg,#8fb8e0,#d8dde2 45%,#7b8a6a)}
.p3{background:linear-gradient(180deg,#6fa0d6,#e8ecef 45%,#6f9a54)}
.p4{background:linear-gradient(180deg,#4f86c4,#3f6f9c 55%,#8b6f58)}
.scrollbar{height:5px;background:#ccc;margin-top:6px;position:relative}
.scrollbar span{position:absolute;left:24px;top:0;width:120px;height:5px;background:#333}

/* CTA */
.cta{position:absolute;left:133px;top:2425px;width:934px;text-align:center}
.cta h2{font-family:"Lora",Georgia,serif;font-weight:400;color:var(--jade);font-size:24px;text-transform:uppercase}
.cta .btn{margin-top:16px;height:38px;line-height:38px;font-size:13px}

/* Footer */
.site-footer{position:absolute;left:0;top:2594px;width:1200px;height:97px;background:var(--footer);color:#cfcfcf}
.footer-links{position:absolute;left:133px;top:26px;font-size:11.5px}
.footer-links a{color:#cfcfcf;text-decoration:none}
.footer-links .sep{margin:0 8px}
.copyright{position:absolute;left:133px;top:52px;font-size:11.5px}
.site-footer .social{top:38px}
</style>
</head>
<body>

<header class="top-bar">
  <svg class="stripes" width="1200" height="145" aria-hidden="true">
    <defs>
      <linearGradient id="darkSide" x1="0" y1="0" x2="1" y2="0">
        <stop offset="0" stop-color="#6a6a6a"/>
        <stop offset="1" stop-color="#3f3f3f"/>
      </linearGradient>
    </defs>
    <polygon points="898,0 1200,0 1200,145 778,145" fill="url(#darkSide)"/>
    <polygon points="860,0 882,0 762,145 740,145" fill="#5a5a5a" opacity=".55"/>
    <polygon points="884,0 897,0 777,145 764,145" fill="#ffffff"/>
  </svg>
  <div class="brand">
    <span class="brand-mark"></span>
    <span class="brand-name">ORBIN FUNDING<span class="sub">GROUP</span></span>
  </div>
  <div class="contact-info">
    <div class="phone">
      <svg width="18" height="18" viewBox="0 0 24 24" aria-hidden="true"><path fill="#fff" d="M6.6 10.8a15 15 0 0 0 6.6 6.6l2.2-2.2c.3-.3.7-.4 1-.2 1.1.4 2.3.6 3.6.6.6 0 1 .4 1 1V20c0 .6-.4 1-1 1A17 17 0 0 1 3 4c0-.6.4-1 1-1h3.5c.6 0 1 .4 1 1 0 1.3.2 2.5.6 3.6.1.3 0 .7-.2 1z"/></svg>
      <span>555 014 2290</span>
    </div>
    <div class="email">
      <svg width="13" height="10" viewBox="0 0 13 10" aria-hidden="true"><rect width="13" height="10" rx="1" fill="#fff"/><path d="M0 1l6.5 5L13 1" stroke="#777" fill="none"/></svg>
      <span>info@orbinfunding.example</span>
    </div>
  </div>
</header>

<nav class="main-nav">
  <ul>
    <li><a class="current" href="#">Home</a></li>
    <li><a href="#">About</a></li>
    <li><a href="#">Team</a></li>
    <li><a href="#">Services</a></li>
    <li><a href="#">Project Experience</a></li>
    <li><a href="#">Contact</a></li>
  </ul>
  <div class="social"><span></span><span></span><span></span><span></span></div>
</nav>

<section class="hero" role="img" aria-label="City skyline at dusk with a businessman in a suit looking out, video placeholder">
  <svg class="play" viewBox="0 0 52 52" aria-hidden="true"><circle cx="26" cy="26" r="25" fill="#fff"/><polygon points="20,15 20,37 38,26" fill="#222"/></svg>
</section>

<section class="welcome">
  <h1>Welcome to Orbin Funding Group</h1>
  <p>Orbin Funding Group Limited is a private property finance company. Orbin Funding Group has capital to directly fund first mortgage, mezzanine and preferred equity financing. We also acquire performing, sub-performing and distressed debt.</p>
  <p>Orbin Fundings management philosophy emphasises expertise, innovation, wisdom, honesty and competitiveness. Orbin Funding are not finance brokers - we provide debt funding to the commercial property and residential development sectors. Our process is built from experience and cumutavely Orbin Fundings Directors have in excess of 60 years wisdom</p>
  <a class="btn" href="#">View Our Team</a>
</section>

<section class="services">
  <article class="service-text">
    <h2>First Mortgage</h2>
    <p>Fusce nec leo ac urna pulvinar auctor. Mauris bibendum fringilla velit. Nulla in lorem at massa pellentesque posuere. Nulla tristique posuere molestie. Aliquam erat volutpat. Etiam quis aliquet risus. Duis ornare erat eget magna dapibus, in accumsan quam pharetra. Nam tempus, quam in bibendum vulputate, sapien dolor viverra nisl, vitae euismod elit turpis et nulla. Aliquam erat volutpat. Pellentesque blandit lacus eget nunc faucibus.</p>
    <a class="outline-btn" href="#">Read more</a>
  </article>
  <div class="photo photo-desk" role="img" aria-label="Hands signing a mortgage document at a desk"></div>
  <div class="photo photo-coins" role="img" aria-label="Hand stacking coins in warm light"></div>
  <article class="service-text">
    <h2>Equity Financing</h2>
    <p>Fusce nec leo ac urna pulvinar auctor. Mauris bibendum fringilla velit. Nulla in lorem at massa pellentesque posuere. Nulla tristique posuere molestie. Aliquam erat volutpat. Etiam quis aliquet risus. Duis ornare erat eget magna dapibus, in accumsan quam pharetra. Nam tempus, quam in bibendum vulputate, sapien dolor viverra nisl, vitae euismod elit turpis et nulla. Aliquam erat volutpat. Pellentesque blandit lacus eget nunc faucibus.</p>
    <a class="outline-btn" href="#">Read more</a>
  </article>
  <article class="service-text">
    <h2>Sub-Performing and<br>Distressed Debt</h2>
    <p>Fusce nec leo ac urna pulvinar auctor. Mauris bibendum fringilla velit. Nulla in lorem at massa pellentesque posuere. Nulla tristique posuere molestie. Aliquam erat volutpat. Etiam quis aliquet risus. Duis ornare erat eget magna dapibus, in accumsan quam pharetra. Nam tempus, quam in bibendum vulputate, sapien dolor viverra nisl, vitae euismod.</p>
    <a class="outline-btn" href="#">Read more</a>
  </article>
  <div class="photo photo-blue" role="img" aria-label="Blue-toned coin stacks over financial figures"></div>
</section>

<section class="projects">
  <h2>Project Experience</h2>
  <div class="project-row">
    <div class="p1" role="img" aria-label="Glass office building at dusk"></div>
    <div class="p2" role="img" aria-label="Modern office campus with landscaped plaza"></div>
    <div class="p3" role="img" aria-label="White modern office block with lawn"></div>
    <div class="p4" role="img" aria-label="Glass office towers beside a walkway"></div>
  </div>
  <div class="scrollbar"><span></span></div>
</section>

<section class="cta">
  <h2>Vestibulum condimentum, risus ut posuere cursus</h2>
  <a class="btn" href="#">Contact Us</a>
</section>

<footer class="site-footer">
  <div class="footer-links">
    <a href="#">Home</a><span class="sep">|</span><a href="#">About</a><span class="sep">|</span><a href="#">Team</a><span class="sep">|</span><a href="#">Services</a><span class="sep">|</span><a href="#">Project Experience</a><span class="sep">|</span><a href="#">Contact</a>
  </div>
  <div class="copyright">Copyright &copy; 2017 &nbsp;Orbin Funding Group. &nbsp;All rights reserved.</div>
  <div class="social"><span></span><span></span><span></span><span></span></div>
</footer>

</body>
</html>
```